Presentation Folder, for Cancer Awareness, VERY COLORFULL AND MODERN

This will be a standard size folder that will hold standard 8 1/2 x 11 papers with a business card slot on the flap, this is a very easy project with very little text and the design for the back page is already done so all you really have to do is make a very nice colorful front cover, you will see my attachments are labeled and I gave you alot of instructions, this should be a very fast easy project
Updates

Reason: there has not been enough quality designs, sorry

Target Market(s)

Our Target Market is Dr's that Deal with Cancer patients

Industry/Entity Type

Healthcare

Font styles to use
Serif

Colors

Designer to choose colors to be used in the design.

Requirements
Must have
• Project must be tasteful and look professional with the ribbons as the main focal point in the center of folder the folder should be a nice gray color to accent the color of the ribbons , the back page needs no design it is the" Sorvane Test" in the attachments I sent
Nice to have
• I would like the ribbons displayed in a row, I included a logo sample layout
• a picture on the front of the folder under the words Hereditary Cancer Screening - Then under that put the words - The Power of Knowledge - then add the picture I labeled Great Picture in the attachments

```html
<!DOCTYPE html>
<html lang="en">
<head>
<meta charset="utf-8">
<title>Hereditary Cancer Screening Folder</title>
<link href="https://fonts.googleapis.com/css2?family=Lato:ital,wght@0,300;0,400;0,700;0,900;1,900&display=swap" rel="stylesheet">
<style>
  :root{
    --backdrop:#3b3b3c;
    --paper:#f4f4f6;
    --paper-shade:#e6e6ea;
    --magenta:#c0336f;
    --ink:#3a3a3e;
    --ink-soft:#6b6b72;
    --row-a:#e9e9ed;
    --row-b:#f7f7f9;
    --lynch:#e0b12e;
    --peutz:#a5bd35;
    --lifraumeni:#4a9d47;
    --cowden:#3b80cc;
    --diffuse:#58585c;
  }
  *{box-sizing:border-box;margin:0;padding:0}
  html,body{width:1200px;height:789px;overflow:hidden}
  body{background:var(--backdrop);font-family:"Lato",sans-serif;color:var(--ink);position:relative}

  .folder{position:absolute;left:70px;top:30px;width:1060px;height:729px;display:flex;box-shadow:0 10px 30px rgba(0,0,0,.45)}
  .page{position:relative;width:530px;height:729px;background:var(--paper);overflow:hidden}
  .page--back{background:linear-gradient(90deg,var(--paper) 0%,var(--paper) 88%,var(--paper-shade) 100%)}
  .page--front{background:linear-gradient(90deg,var(--paper-shade) 0%,var(--paper) 8%,#fbfbfc 100%)}

  /* back page */
  .brand-block{position:absolute;left:44px;top:52px}
  .brand-name{font-size:15px;font-weight:400;letter-spacing:3px;color:var(--magenta);display:flex;align-items:center;gap:6px}
  .brand-dot{width:8px;height:8px;border-radius:50%;background:var(--magenta)}
  .brand-contact{font-size:6.5px;color:var(--ink-soft);margin-top:4px;letter-spacing:.3px;line-height:1.4}
  .menu-title{position:absolute;right:60px;top:48px;text-align:right}
  .menu-title h2{font-size:19px;font-weight:900;font-style:italic;color:var(--magenta)}
  .menu-title p{font-size:6.5px;color:var(--ink-soft);letter-spacing:.4px;margin-top:2px}

  .gene-table{position:absolute;left:44px;top:104px;width:410px;border-collapse:collapse;font-size:8px}
  .gene-table th{background:var(--magenta);color:#fff;font-weight:400;text-transform:uppercase;height:15px;text-align:left;padding:0 6px;font-size:8px;letter-spacing:.3px}
  .gene-table th.organ-head{text-align:center}
  .gene-table td{height:14px;padding:0 6px;white-space:nowrap}
  .gene-table td.gene{color:var(--magenta);font-weight:700;width:92px}
  .gene-table td.organ{color:var(--ink);font-weight:700}
  .gene-table tr:nth-child(odd) td{background:var(--row-a)}
  .gene-table tr:nth-child(even) td{background:var(--row-b)}
  .gene-table tr.group td{color:#fff;text-transform:uppercase;font-weight:400;letter-spacing:.4px;height:13px;padding-left:14px}
  .group--lynch td{background:var(--lynch)!important}
  .group--peutz td{background:var(--peutz)!important}
  .group--lifraumeni td{background:var(--lifraumeni)!important}
  .group--cowden td{background:var(--cowden)!important}
  .group--diffuse td{background:var(--diffuse)!important}

  /* front page */
  .cover-title{position:absolute;left:0;right:0;top:82px;text-align:center}
  .cover-title h1{font-size:25px;font-weight:400;color:var(--magenta)}
  .cover-title p{font-size:17px;font-weight:300;color:var(--ink);margin-top:2px}
  .family-photo{position:absolute;left:60px;top:150px;width:460px;height:230px;
    background:radial-gradient(ellipse at 60% 45%,rgba(205,200,195,.75) 0%,rgba(225,222,220,.5) 45%,rgba(250,250,251,0) 75%)}
  .ribbon-art{position:absolute;left:212px;top:168px;width:130px;height:210px}
  .cancer-types{position:absolute;left:0;right:0;top:390px;text-align:center;font-size:16.5px;font-weight:300;color:var(--ink);line-height:1.55}
  .cover-brand{position:absolute;left:210px;top:566px;width:120px;display:flex;flex-direction:column;align-items:center;gap:10px;background:#fff;padding:12px 0 10px}
  .cover-brand .brand-dot{width:18px;height:18px}
  .cover-brand span{font-size:9px;letter-spacing:1.5px;color:var(--ink)}
</style>
</head>
<body>
<div class="folder">
  <section class="page page--back">
    <div class="brand-block">
      <div class="brand-name"><span class="brand-dot"></span>VERANTHE DIAGNOSTICS</div>
      <div class="brand-contact">820 Larkmoor Avenue Suite 4 Brenton GA 30990<br>(555) 014-2270 | hello@veranthe-dx.com</div>
    </div>
    <div class="menu-title">
      <h2>Sorvane Test Menu</h2>
      <p>CLIENT SERVICES | VERANTHE-DX.COM</p>
    </div>
    <table class="gene-table">
      <thead><tr><th>Gene</th><th class="organ-head">Cancer-Associated Organ/Systems</th></tr></thead>
      <tbody>
        <tr><td class="gene">APC</td><td class="organ">Colon</td></tr>
        <tr><td class="gene">ATM</td><td class="organ">Breast/Pancreatic/Brain</td></tr>
        <tr><td class="gene">BARD1</td><td class="organ">Breast/Ovarian</td></tr>
        <tr><td class="gene">BMPR1A</td><td class="organ">Colon</td></tr>
        <tr><td class="gene">BRCA1</td><td class="organ">Breast/Ovarian/Prostate</td></tr>
        <tr><td class="gene">BRCA2</td><td class="organ">Breast/Ovarian/Prostate</td></tr>
        <tr><td class="gene">BRIP1</td><td class="organ">Breast/Ovarian</td></tr>
        <tr><td class="gene">CDK4</td><td class="organ">Melanoma</td></tr>
        <tr><td class="gene">P16 (CDKN2A)</td><td class="organ">Melanoma/Breast/Pancreatic/Squamous</td></tr>
        <tr><td class="gene">FANCC</td><td class="organ">Blood</td></tr>
        <tr><td class="gene">MEN1</td><td class="organ">Thyroid/Parathyroid</td></tr>
        <tr><td class="gene">MET</td><td class="organ">Renal/Hepatic</td></tr>
        <tr><td class="gene">MRE11A</td><td class="organ">Ovarian/Breast</td></tr>
        <tr><td class="gene">NBN</td><td class="organ">Breast/Ovarian/Prostate/Melanoma</td></tr>
        <tr><td class="gene">NF1</td><td class="organ">Blood</td></tr>
        <tr><td class="gene">NTRK1</td><td class="organ">Thyroid/Parathyroid</td></tr>
        <tr><td class="gene">PALB2</td><td class="organ">Breast/Ovarian/Pancreatic</td></tr>
        <tr><td class="gene">PTCH1</td><td class="organ">Melanoma/Brain/Breast/Colon</td></tr>
        <tr><td class="gene">RAD50</td><td class="organ">Breast/Ovarian</td></tr>
        <tr><td class="gene">RAD51C</td><td class="organ">Ovarian/Breast</td></tr>
        <tr><td class="gene">RAD51D</td><td class="organ">Ovarian/Breast</td></tr>
        <tr><td class="gene">RET</td><td class="organ">Lung/Thyroid/Parathyroid</td></tr>
        <tr><td class="gene">SMAD4</td><td class="organ">Colon/Pancreas</td></tr>
        <tr class="group group--lynch"><td colspan="2">Lynch Syndrome Genes</td></tr>
        <tr><td class="gene">MLH1</td><td class="organ">Colorectal/Ovarian</td></tr>
        <tr><td class="gene">MSH2</td><td class="organ">Colorectal/Ovarian</td></tr>
        <tr><td class="gene">MSH6</td><td class="organ">Colorectal/Ovarian</td></tr>
        <tr><td class="gene">PMS2</td><td class="organ">Colorectal/Ovarian</td></tr>
        <tr><td class="gene">EPCAM</td><td class="organ">Colorectal</td></tr>
        <tr class="group group--peutz"><td colspan="2">Peutz-Jeghers Syndrome Gene</td></tr>
        <tr><td class="gene">STK11</td><td class="organ">Breast/Ovarian/Melanoma/Colorectal/Lung</td></tr>
        <tr class="group group--lifraumeni"><td colspan="2">Li-Fraumeni Syndrome Gene</td></tr>
        <tr><td class="gene">CHEK2</td><td class="organ">Breast/Ovarian/Prostate</td></tr>
        <tr><td class="gene">TP53</td><td class="organ">Breast/Bladder/Ovarian/Prostate/Lung</td></tr>
        <tr class="group group--cowden"><td colspan="2">Cowden Syndrome Gene</td></tr>
        <tr><td class="gene">PTEN</td><td class="organ">Endometrium/Breast/Prostate/Lung</td></tr>
        <tr class="group group--diffuse"><td colspan="2">Hereditary Diffuse Gastric Cancer Syndrome Gene</td></tr>
        <tr><td class="gene">CDH1</td><td class="organ">Breast/Gastric/Ovarian/Prostate</td></tr>
        <tr><td class="gene">VHL</td><td class="organ">Renal</td></tr>
      </tbody>
    </table>
  </section>

  <section class="page page--front">
    <div class="cover-title">
      <h1>Hereditary Cancer Screening</h1>
      <p>The Power of Knowledge</p>
    </div>
    <div class="family-photo" role="img" aria-label="Faded photograph of a multi-generation family sharing a meal at a table"></div>
    <svg class="ribbon-art" viewBox="0 0 130 210" role="img" aria-label="Pink awareness ribbon illustration with two clasped hands at its crossing">
      <ellipse cx="65" cy="105" rx="58" ry="100" fill="#c0336f" opacity=".85"/>
    </svg>
    <div class="cancer-types">
      Breast | Ovarian | Endometrial &nbsp;| Gastric | Colorectal<br>
      Pancreatic | Melanoma | Prostate | Lung | Colon
    </div>
    <div class="cover-brand">
      <span class="brand-dot"></span>
      <span>VERANTHE DIAGNOSTICS</span>
    </div>
  </section>
</div>
</body>
</html>
```